Quillmarsh Property Solutions need a business card design

Hello guys. We would need a business card design asap please.
We are a start up property investment business based in London UK specialised in buying, selling, managing and letting properties and helping distressed property owners.
The name of our Business is Quillmarsh, the logo symbolises the four fundamental elements of the world (earth, air, fire and water) and so it stands for strength, stability, longevity.
We would like the business card to communicate professionalism and reliability. Many many thanks indeed for your work.

Details:

1.) Rosalind Updike
Property Investor
Mobile: +44(0)7700123456
Email: rosalind.quillmarsh@mailbox-example.com

2.) Dominic Updike
Property Investor
Mobile: +44(0)7700987654
Email: dominic.quillmarsh@mailbox-example.com

```html
<!DOCTYPE html>
<html lang="en">
<head>
<meta charset="utf-8">
<title>Quillmarsh Property Solutions – Business Card</title>
<link rel="stylesheet" href="https://fonts.googleapis.com/css2?family=Lato:wght@400;700;900&display=swap">
<style>
  :root {
    --page-bg: #e6e6e6;
    --card-white: #ffffff;
    --card-black: #050505;
    --ink-black: #111111;
    --ink-grey: #b9b9b9;
    --navy: #1f3a8a;
    --brand-red: #c8202a;
    --brand-green: #10913f;
    --brand-blue: #2550a8;
    --divider: #555555;
  }
  * { box-sizing: border-box; margin: 0; padding: 0; }
  html, body {
    width: 1200px; height: 926px; overflow: hidden;
    background: var(--page-bg);
    font-family: "Lato", sans-serif;
  }
  .sheet {
    width: 1200px; height: 926px;
    display: flex; flex-direction: column; align-items: center;
    justify-content: center; gap: 28px;
  }
  .card {
    position: relative; width: 720px; height: 410px; overflow: hidden;
    box-shadow: 0 4px 14px rgba(0,0,0,.18);
  }
  /* Front */
  .card--front { background: var(--card-white); }
  .waves { position: absolute; left: 0; top: 0; width: 100%; height: 100%; }
  .brand { position: absolute; left: 0; right: 0; text-align: center; }
  .card--front .brand { top: 34px; }
  .brand__mark {
    display: block; margin: 0 auto 10px; width: 16px; height: 16px;
    background: var(--brand-red);
  }
  .brand__name {
    display: block; font-weight: 900; letter-spacing: .5px;
    color: var(--ink-black); font-size: 27px; line-height: 1;
  }
  .brand__tagline {
    display: block; font-weight: 700; color: var(--ink-black);
    font-size: 10px; letter-spacing: .6px; margin-top: 5px;
  }
  .contacts {
    position: absolute; top: 142px; left: 0; right: 0;
    display: flex; justify-content: center;
  }
  .person { width: 330px; padding: 0 18px; }
  .person--left { text-align: right; border-right: 1px solid var(--divider); }
  .person__name {
    color: var(--navy); font-weight: 700; font-size: 19px;
    letter-spacing: .5px; text-transform: uppercase;
  }
  .person__role { color: var(--brand-red); font-weight: 700; font-size: 13.5px; margin-bottom: 8px; }
  .person__line { color: var(--navy); font-size: 12.5px; line-height: 1.7; white-space: nowrap; }
  .person__key { color: var(--brand-green); font-weight: 700; }
  /* Back */
  .card--back { background: var(--card-black); }
  .card--back .brand { top: 150px; }
  .card--back .brand__mark { width: 22px; height: 22px; margin-bottom: 18px; }
  .card--back .brand__name { color: var(--ink-grey); font-size: 40px; font-weight: 700; letter-spacing: 2px; }
  .card--back .brand__tagline { color: var(--ink-grey); font-size: 15px; font-weight: 400; letter-spacing: 1.5px; margin-top: 8px; }
</style>
</head>
<body>
<main class="sheet">
  <section class="card card--front" aria-label="Business card front">
    <svg class="waves" viewBox="0 0 720 410" preserveAspectRatio="none" aria-hidden="true">
      <path d="M0,258 C170,318 420,340 720,350 L720,410 L0,410 Z" fill="var(--brand-green)"/>
      <path d="M0,290 C190,338 430,356 720,356 L720,410 L0,410 Z" fill="var(--brand-red)"/>
      <path d="M0,306 C200,350 440,366 720,364 L720,410 L0,410 Z" fill="var(--brand-blue)"/>
    </svg>
    <div class="brand">
      <span class="brand__mark"></span>
      <span class="brand__name">QUILLMARSH</span>
      <span class="brand__tagline">PROPERTY SOLUTIONS</span>
    </div>
    <div class="contacts">
      <div class="person person--left">
        <p class="person__name">Dominic Updike</p>
        <p class="person__role">Property Investor</p>
        <p class="person__line">+44(0)7700987654 : <span class="person__key">M</span></p>
        <p class="person__line">dominic.quillmarsh@mailbox-example.com : <span class="person__key">E</span></p>
      </div>
      <div class="person person--right">
        <p class="person__name">Rosalind Updike</p>
        <p class="person__role">Property Investor</p>
        <p class="person__line"><span class="person__key">M</span> : +44(0)7700123456</p>
        <p class="person__line"><span class="person__key">E</span> : rosalind.quillmarsh@mailbox-example.com</p>
      </div>
    </div>
  </section>

  <section class="card card--back" aria-label="Business card back">
    <div class="brand">
      <span class="brand__mark"></span>
      <span class="brand__name">QUILLMARSH</span>
      <span class="brand__tagline">PROPERTY SOLUTIONS</span>
    </div>
  </section>
</main>
</body>
</html>
```